Company or website name
- www.keyzUPdone.com
- Links to the website
- keyzupdone.com
- Describe your company and organization and target audience
- My name is dwight pelham from houston texas. I am a realtor. I have been trying very hard to develop a site that not only reflects me but can generate some business. I have a site with an idx search but it is too expensive and I really dont think IDX is the way to go. I just want a site that is neat and holds people interest. For this contest, I pretty much did all the work. I need your creativity. I have a file crate link that has everything in it. Each section is marked. I have about me, about what I do, How i am different, Neighborhoods i specialize in etc.
- The design should have the following
- I want in my site the following: I would Live Feed of my Snapvane and Friendloop page on the first main page I want my video playing as the main shot. I have 2 give a ways (something of value), buyers handbook and sellers handbook I do a monthly newsletter i would also like to give some attention to. I want a chat box that is either a bot or goes into text message to me www.keyzUPdone.com is the website url filecratr link: https://www.filecratr.net/sh/9kqpz27xw4ab51/BBTrq_7LmQ2hzxvNcPwYdKeRt?dl=0 If you can use the idx's that my assocation provides that would be great. I have been told they are frames, it is ok if you dont but if you can they do have some great info.

```html
<!DOCTYPE html>
<html lang="en">
<head>
<meta charset="utf-8">
<title>Dwight Pelham — Houston Realtor</title>
<link href="https://fonts.googleapis.com/css2?family=Montserrat:wght@400;500;600;700&family=Open+Sans:wght@400;600;700&display=swap" rel="stylesheet">
<style>
:root{
  --red:#cf1f35;
  --ink:#2a2a2a;
  --text:#555;
  --muted:#8a8a8a;
  --line:#e3e3e3;
  --footer:#2f2f31;
  --footer-deep:#222224;
  --white:#fff;
}
*{margin:0;padding:0;box-sizing:border-box}
html,body{width:1200px;height:3527px;overflow:hidden}
body{font-family:"Open Sans",Arial,sans-serif;color:var(--text);background:var(--white);position:relative;font-size:13px}
h1,h2,h3,h4,.brand,.nav{font-family:"Montserrat",Arial,sans-serif}

.site-header{position:absolute;top:0;left:0;width:1200px;height:65px;background:var(--white);box-shadow:0 1px 4px rgba(0,0,0,.08);z-index:2}
.brand{position:absolute;left:40px;top:20px;display:flex;align-items:center;gap:8px;font-weight:600;font-size:17px;color:var(--red)}
.brand .mark{width:16px;height:16px;background:var(--red)}
.utility{position:absolute;right:40px;top:7px;font-size:11px;color:var(--muted);display:flex;gap:18px}
.utility b{color:var(--ink);font-weight:600}
.nav{position:absolute;right:40px;top:33px;display:flex;gap:26px;font-size:12px;font-weight:600;color:var(--ink);text-transform:uppercase}
.nav .active{color:var(--red)}

.hero{position:absolute;top:65px;left:0;width:1200px;height:610px;background:linear-gradient(160deg,#dfe4e7 0%,#a8b2b8 35%,#5b6368 60%,#2e3338 78%,#4b5a3f 100%)}
.play{position:absolute;left:545px;top:250px}

.search-band{position:absolute;top:675px;left:0;width:1200px;height:125px}
.search-band h2{position:absolute;top:28px;width:100%;text-align:center;font-size:16px;font-weight:500;color:var(--ink)}
.search-box{position:absolute;left:360px;top:60px;width:480px;height:34px;border:1px solid #cfcfcf;border-radius:3px;display:flex;align-items:center;padding:0 12px;font-size:12px;color:var(--muted);justify-content:space-between}
.red-rule{position:absolute;left:0;top:113px;width:1200px;height:4px;background:var(--red)}

.agent{position:absolute;top:815px;left:0;width:1200px;height:225px}
.agent-photo{position:absolute;left:88px;top:42px;width:125px;height:150px;background:linear-gradient(180deg,#b8bcc2,#6c7480 70%,#3c3f46)}
.agent-info{position:absolute;left:228px;top:46px;width:170px}
.agent-info h3{color:var(--red);font-size:20px;font-weight:600;margin-bottom:6px}
.agent-info p{font-size:11px;line-height:1.5;color:var(--muted)}
.agent-info .phone{margin-top:12px;color:var(--ink);font-weight:600;display:flex;align-items:center;gap:6px}
.btn-sm{display:inline-block;margin-top:14px;background:var(--red);color:#fff;font-size:10px;font-weight:700;padding:5px 16px;border-radius:3px;text-transform:uppercase}
.connection{position:absolute;left:410px;top:30px;width:790px;height:185px;background:var(--red);clip-path:polygon(4% 0,100% 0,100% 100%,0 100%)}
.connection h3{text-align:center;color:#fff;font-size:22px;font-weight:600;margin-top:24px}
.connection .sub{text-align:center;color:#ffd9de;font-size:11px;margin-top:6px}
.checks{display:grid;grid-template-columns:1fr 1fr;gap:10px 40px;width:560px;margin:22px auto 0;list-style:none}
.checks li{color:#fff;font-size:12px;display:flex;align-items:center;gap:8px}

.books{position:absolute;top:1070px;left:0;width:1200px;height:390px}
.section-title{font-size:22px;font-weight:500;color:var(--ink);text-align:center}
.books .section-title{margin-top:18px}
.books .divider{position:absolute;left:600px;top:80px;width:1px;height:290px;background:var(--line)}
.book{position:absolute;top:82px;width:160px;height:200px}
.book.buyer{left:355px;background:linear-gradient(135deg,#f2d24a,#d9a725 60%,#6a8f3c)}
.book.seller{left:685px;background:linear-gradient(135deg,#4b8fd6,#2a63a8 60%,#9cc7e8)}
.btn{position:absolute;top:318px;width:140px;height:32px;border-radius:16px;background:var(--red);color:#fff;font-size:12px;font-weight:600;text-align:center;line-height:32px}

.lined-title{position:absolute;left:0;width:1200px;display:flex;align-items:center;justify-content:center;gap:22px}
.lined-title span{width:140px;height:1px;background:#e7b3ba}
.lined-title h2{font-size:22px;font-weight:500;color:var(--ink);text-transform:uppercase;letter-spacing:1px}

.listings{position:absolute;top:1625px;left:172px;display:flex;gap:12px}
.listing{position:relative;width:206px;height:280px;overflow:hidden}
.listing .photo{position:absolute;inset:0}
.listing .meta{position:absolute;left:0;bottom:0;width:100%;height:70px;background:linear-gradient(transparent,rgba(0,0,0,.7));color:#fff;padding:22px 12px 0}
.listing .price{font-family:"Montserrat",sans-serif;font-weight:700;font-size:16px;line-height:1.2}
.listing .specs{font-size:10px;margin-top:4px;opacity:.9;line-height:1.3}
.arrow{position:absolute;top:1748px}

.post{position:absolute;width:400px;height:195px}
.post .thumb{position:absolute;left:0;top:0;width:128px;height:180px}
.post .body{position:absolute;left:148px;top:0;width:240px}
.post h4{font-size:14px;font-weight:600;color:var(--ink);line-height:1.35;margin-bottom:8px}
.post p{font-size:11px;line-height:1.6;color:var(--muted)}
.post .more{font-size:11px;color:var(--ink);text-decoration:underline;margin-top:8px;display:block}
.load-more{position:absolute;top:2545px;width:1200px;text-align:center;font-size:12px;color:var(--ink)}

.communities-photo{position:absolute;top:2690px;left:0;width:1200px;height:535px;background:linear-gradient(180deg,#3f5a2b 0%,#5e7d3a 35%,#86934f 60%,#9a9d7c 80%,#6f7a66 100%)}
.communities-band{position:absolute;top:2885px;left:0;width:1200px;height:145px;background:rgba(20,20,20,.55);color:#fff}
.communities-band h3{text-align:center;font-size:17px;font-weight:500;margin-top:22px}
.community-cols{display:flex;justify-content:center;gap:120px;margin-top:22px}
.community-cols ul{list-style:none;font-size:12px;line-height:2}

.footer{position:absolute;top:3225px;left:0;width:1200px;height:215px;background:var(--footer);color:#bdbdbd;font-size:11px}
.footer .about{position:absolute;left:40px;top:40px;width:420px;line-height:1.6}
.footer .about strong{color:#fff;display:block;margin:14px 0 4px}
.footer .badge{position:absolute;left:500px;top:60px;width:40px;height:28px;background:#5a5a5c}
.footer .badge-text{position:absolute;left:552px;top:60px;width:200px;line-height:1.5}
.footer .news{position:absolute;left:800px;top:40px;width:360px;line-height:1.6}
.footer .news-form{display:flex;margin-top:14px}
.footer .news-form div{flex:1;height:30px;background:#fff;border-radius:3px 0 0 3px;color:var(--muted);padding:7px 10px}
.footer .news-form b{background:var(--red);color:#fff;padding:0 14px;line-height:30px;border-radius:0 3px 3px 0;font-weight:600}
.bottom-bar{position:absolute;top:3440px;left:0;width:1200px;height:87px;background:var(--footer-deep);color:#9a9a9a;font-size:11px}
.bottom-bar .copy{position:absolute;left:40px;top:30px}
.bottom-bar .links{position:absolute;right:120px;top:30px;display:flex;gap:28px}
.chat{position:absolute;left:1118px;top:3378px;width:58px;height:58px;border-radius:50%;background:var(--red);color:#fff;font-weight:700;font-size:13px;text-align:center;line-height:58px;box-shadow:0 2px 6px rgba(0,0,0,.3)}
</style>
</head>
<body>

<header class="site-header">
  <div class="brand"><span class="mark"></span>keyzupdone.com</div>
  <div class="utility"><span><b>(713) 555-0142</b></span><span>Login</span><span>Register</span></div>
  <nav class="nav">
    <span class="active">Home</span><span>Search</span><span>Buy</span><span>Sell</span><span>Communities</span><span>Meet Dwight</span><span>Reviews</span><span>Contact</span>
  </nav>
</header>

<section class="hero" role="img" aria-label="Video still of a modern white two-storey home with glass walls and a pool terrace">
  <svg class="play" width="110" height="110" viewBox="0 0 110 110" aria-hidden="true">
    <circle cx="55" cy="55" r="50" fill="none" stroke="#fff" stroke-width="5"/>
    <polygon points="44,34 44,76 79,55" fill="#fff"/>
  </svg>
</section>

<section class="search-band">
  <h2>Discover Your Dream Home</h2>
  <div class="search-box"><span>Search by city, zip or neighborhood</span>
    <svg width="14" height="14" viewBox="0 0 14 14" aria-hidden="true"><circle cx="6" cy="6" r="4.5" fill="none" stroke="#666" stroke-width="1.5"/><line x1="9.5" y1="9.5" x2="13" y2="13" stroke="#666" stroke-width="1.5"/></svg>
  </div>
  <div class="red-rule"></div>
</section>

<section class="agent">
  <div class="agent-photo" role="img" aria-label="Portrait photo of realtor Dwight Pelham"></div>
  <div class="agent-info">
    <h3>Dwight Pelham</h3>
    <p>Realtor, Houston TX<br>Harborline Realty Group<br>Buyers &amp; Sellers Agent</p>
    <div class="phone">
      <svg width="12" height="12" viewBox="0 0 12 12" aria-hidden="true"><path d="M2.5 1 L4.5 1 L5.5 3.5 L4.2 4.5 Q5 6.8 7.5 7.8 L8.5 6.5 L11 7.5 L11 9.5 Q10.5 11 9 11 Q1 10 1 3 Q1 1.5 2.5 1Z" fill="#cf1f35"/></svg>
      (713) 555-0142
    </div>
    <span class="btn-sm">Contact</span>
  </div>
  <div class="connection">
    <h3>Your Local Real Estate Connection</h3>
    <p class="sub">Honest advice, sharp pricing and a neighbor who knows Houston block by block.</p>
    <ul class="checks">
      <li><svg width="12" height="12" viewBox="0 0 12 12"><path d="M1 6 L4.5 9.5 L11 2.5" stroke="#fff" stroke-width="2" fill="none"/></svg>Local market pricing expertise</li>
      <li><svg width="12" height="12" viewBox="0 0 12 12"><path d="M1 6 L4.5 9.5 L11 2.5" stroke="#fff" stroke-width="2" fill="none"/></svg>Free buyer and seller handbooks</li>
      <li><svg width="12" height="12" viewBox="0 0 12 12"><path d="M1 6 L4.5 9.5 L11 2.5" stroke="#fff" stroke-width="2" fill="none"/></svg>Smart marketing for every listing</li>
      <li><svg width="12" height="12" viewBox="0 0 12 12"><path d="M1 6 L4.5 9.5 L11 2.5" stroke="#fff" stroke-width="2" fill="none"/></svg>Monthly neighborhood newsletter</li>
      <li><svg width="12" height="12" viewBox="0 0 12 12"><path d="M1 6 L4.5 9.5 L11 2.5" stroke="#fff" stroke-width="2" fill="none"/></svg>Skilled contract negotiation</li>
      <li><svg width="12" height="12" viewBox="0 0 12 12"><path d="M1 6 L4.5 9.5 L11 2.5" stroke="#fff" stroke-width="2" fill="none"/></svg>Fast replies by text or chat</li>
    </ul>
  </div>
</section>

<section class="books">
  <h2 class="section-title">Download My Book for Free</h2>
  <div class="book buyer" role="img" aria-label="Cover of the buyers handbook"></div>
  <div class="btn" style="left:365px">Download</div>
  <div class="divider"></div>
  <div class="book seller" role="img" aria-label="Cover of the sellers handbook"></div>
  <div class="btn" style="left:695px">Download</div>
</section>

<div class="lined-title" style="top:1515px"><span></span><h2>Featured Listing</h2><span></span></div>
<svg class="arrow" style="left:120px" width="18" height="26" viewBox="0 0 18 26" aria-hidden="true"><polygon points="16,1 2,13 16,25" fill="#cf1f35"/></svg>
<svg class="arrow" style="left:1062px" width="18" height="26" viewBox="0 0 18 26" aria-hidden="true"><polygon points="2,1 16,13 2,25" fill="#cf1f35"/></svg>
<div class="listings">
  <article class="listing"><div class="photo" role="img" aria-label="Brick ranch home with green lawn" style="background:linear-gradient(180deg,#8fb3d9 0%,#a9c4de 35%,#8b6a4f 55%,#5f8a3a 80%)"></div>
    <div class="meta"><div class="price">$399,990</div><div class="specs">4 bd · 3 ba · 2,450 sqft</div></div></article>
  <article class="listing"><div class="photo" role="img" aria-label="Commercial building with parking lot" style="background:linear-gradient(180deg,#7ea8d6 0%,#b9cde2 40%,#9a9a95 60%,#6d6d6a 85%)"></div>
    <div class="meta"><div class="price">$399,990</div><div class="specs">3 bd · 2 ba · 1,980 sqft</div></div></article>
  <article class="listing"><div class="photo" role="img" aria-label="Kitchen with wood cabinets" style="background:linear-gradient(160deg,#e9e2d6 0%,#b78a5e 45%,#7a5535 75%,#d8cfc2)"></div>
    <div class="meta"><div class="price">$399,990</div><div class="specs">3 bd · 2 ba · 2,120 sqft</div></div></article>
  <article class="listing"><div class="photo" role="img" aria-label="Bright living room interior" style="background:linear-gradient(160deg,#f1ece4 0%,#cbb9a3 40%,#8e7a66 75%,#e6ddd0)"></div>
    <div class="meta"><div class="price">$399,990</div><div class="specs">5 bd · 4 ba · 3,300 sqft</div></div></article>
</div>

<div class="lined-title" style="top:2000px"><span></span><h2>Recent Post</h2><span></span></div>
<article class="post" style="left:172px;top:2085px">
  <div class="thumb" role="img" aria-label="Sunlit living room with curtains" style="background:linear-gradient(160deg,#efe6d6,#c9b08a 60%,#8c7354)"></div>
  <div class="body"><h4>13 DIY Improvements to Make Your Home Cleaner</h4>
  <p>Small weekend projects can make a home feel fresher, brighter and easier to sell. Here are simple upgrades buyers notice the moment they walk in the door.</p><span class="more">Read more</span></div>
</article>
<article class="post" style="left:622px;top:2085px">
  <div class="thumb" role="img" aria-label="Couple reviewing paperwork at home" style="background:linear-gradient(160deg,#dfe3e6,#9aa3aa 55%,#5e656b)"></div>
  <div class="body"><h4>When to Get Excited About the Housing Market</h4>
  <p>Rates, inventory and days on market all tell a story. Learn which local signals matter most before you decide it is time to buy or list.</p><span class="more">Read more</span></div>
</article>
<article class="post" style="left:172px;top:2300px">
  <div class="thumb" role="img" aria-label="Family on a home balcony" style="background:linear-gradient(160deg,#e4e6e8,#a9b0b4 50%,#50565a)"></div>
  <div class="body"><h4>Choosing The Right Home</h4>
  <p>Location, layout and long term plans all shape the right choice. Use this quick checklist to compare homes and stay focused on what you need.</p><span class="more">Read more</span></div>
</article>
<article class="post" style="left:622px;top:2300px">
  <div class="thumb" role="img" aria-label="Cozy living room with sofa" style="background:linear-gradient(160deg,#f0e9dc,#c8a97e 55%,#7a6a52)"></div>
  <div class="body"><h4>13 DIY Improvements to Make Your Home Cleaner</h4>
  <p>Fresh paint, clear counters and good lighting go a long way. These easy fixes help your home photograph well and show its best side.</p><span class="more">Read more</span></div>
</article>
<div class="load-more">Load more »</div>

<div class="lined-title" style="top:2625px"><span></span><h2>Communities Served</h2><span></span></div>
<div class="communities-photo" role="img" aria-label="Tree-lined residential street in a Houston neighborhood"></div>
<section class="communities-band">
  <h3>Popular Communities in Houston</h3>
  <div class="community-cols">
    <ul><li>The Heights</li><li>Montrose</li><li>Bellaire</li></ul>
    <ul><li>River Oaks</li><li>Memorial</li><li>Katy</li></ul>
    <ul><li>Sugar Land</li><li>Pearland</li><li>Cypress</li></ul>
  </div>
</section>

<footer class="footer">
  <div class="about">Dwight Pelham is a licensed Texas realtor helping buyers and sellers across greater Houston with honest guidance and local market knowledge. Each office is independently owned and operated.
    <strong>Harborline Realty Group</strong>Houston, Texas · (713) 555-0142</div>
  <div class="badge"></div>
  <div class="badge-text">Equal housing opportunity. Information deemed reliable but not guaranteed.</div>
  <div class="news">Join my monthly newsletter for market updates, new listings and home tips delivered to your inbox.
    <div class="news-form"><div>Your email address</div><b>Subscribe</b></div>
  </div>
</footer>
<div class="bottom-bar">
  <div class="copy">© 2024 Dwight Pelham. All rights reserved.</div>
  <div class="links"><span>Terms of Use</span><span>Privacy</span><span>Sitemap</span><span>Contact</span></div>
</div>
<div class="chat">Chat</div>

</body>
</html>
```